Vantiqo custom business card design

Need a authentic, innovative business card design for a new mobile app business. I am uploading a few screen images from our app for you to view. I would like app design theme to match business card design. I can also send logo images.

```html
<!DOCTYPE html>
<html lang="en">
<head>
<meta charset="utf-8">
<title>Vantiqo Business Card</title>
<link href="https://fonts.googleapis.com/css2?family=Open+Sans:wght@400;600;700;800&display=swap" rel="stylesheet">
<style>
  :root {
    --backdrop: #3a3c40;
    --card-white: #ffffff;
    --card-black: #141414;
    --brand-purple: #5e0a8a;
    --ink: #2b2b2b;
    --ink-soft: #3d3d3d;
    --on-dark: #e8e8e8;
  }
  * { margin: 0; padding: 0; box-sizing: border-box; }
  html, body { width: 1200px; height: 1000px; overflow: hidden; }
  body {
    background: var(--backdrop);
    font-family: "Open Sans", Arial, sans-serif;
    position: relative;
  }
  .card {
    position: absolute;
    left: 250px;
    width: 700px;
    height: 400px;
    border-radius: 3px;
    overflow: hidden;
  }
  /* Back side */
  .card-back {
    top: 50px;
    background: var(--card-black);
  }
  .back-mark {
    position: absolute;
    left: 290px; top: 90px;
    width: 120px; height: 120px;
    border-radius: 50%;
    background: var(--card-white);
  }
  .back-url {
    position: absolute;
    left: 0; right: 0; top: 250px;
    text-align: center;
    color: var(--on-dark);
    font-size: 20px;
    letter-spacing: 6px;
  }
  /* Front side */
  .card-front {
    top: 520px;
    background: var(--card-white);
  }
  .name-band {
    position: absolute;
    left: 0; top: 40px;
    width: 600px; height: 110px;
    background: var(--brand-purple);
    padding: 22px 0 0 70px;
    color: var(--card-white);
  }
  .person-name { font-size: 24px; font-weight: 700; line-height: 1; }
  .person-role { font-size: 17px; font-weight: 400; margin-top: 2px; }
  .brand-block {
    position: absolute;
    left: 600px; top: 40px;
    width: 100px; height: 130px;
    background: var(--card-black);
  }
  .brand-mark {
    position: absolute;
    left: 530px; top: 52px;
    width: 110px; height: 110px;
    border-radius: 50%;
    background: var(--brand-purple);
    border: 4px solid var(--card-white);
  }
  .brand-name {
    position: absolute;
    right: 100px; top: 178px;
    font-size: 40px;
    font-weight: 800;
    color: var(--card-black);
    line-height: 1;
  }
  .contact-list {
    position: absolute;
    left: 70px; top: 228px;
    list-style: none;
  }
  .contact-list li {
    display: flex;
    align-items: center;
    gap: 10px;
    font-size: 19px;
    color: var(--ink);
    height: 27px;
  }
  .contact-icon { width: 18px; height: 18px; fill: var(--brand-purple); }
  .address {
    position: absolute;
    right: 60px; top: 290px;
    text-align: right;
    font-size: 20px;
    line-height: 27px;
    color: var(--ink-soft);
    font-style: normal;
  }
  .address .web { letter-spacing: 2px; }
</style>
</head>
<body>
  <section class="card card-back" aria-label="Card back">
    <div class="back-mark"></div>
    <p class="back-url">vantiqo.com</p>
  </section>

  <section class="card card-front" aria-label="Card front">
    <div class="name-band">
      <p class="person-name">MARCUS LANE</p>
      <p class="person-role">PRESIDENT</p>
    </div>
    <div class="brand-block"></div>
    <div class="brand-mark"></div>
    <p class="brand-name">Vantiqo</p>

    <ul class="contact-list">
      <li>
        <svg class="contact-icon" viewBox="0 0 20 20"><path d="M2 7c0-3 4-5 8-5s8 2 8 5v2h-4V7H6v2H2zM4 11h12l1 7H3z"/></svg>
        555 0142 7731
      </li>
      <li>
        <svg class="contact-icon" viewBox="0 0 20 20"><path d="M6 1h8a1 1 0 0 1 1 1v16a1 1 0 0 1-1 1H6a1 1 0 0 1-1-1V2a1 1 0 0 1 1-1zm1 2v12h6V3z"/></svg>
        555 0186 2094
      </li>
      <li>
        <svg class="contact-icon" viewBox="0 0 20 20"><path d="M5 2h9v5H5zM2 8h16v8H2zm3 9h10v2H5z"/></svg>
        555 0127 4658
      </li>
      <li>
        <svg class="contact-icon" viewBox="0 0 20 20"><path d="M1 4h18v12H1zm1.5 1.5L10 11l7.5-5.5z"/></svg>
        marcus@vantiqo.com
      </li>
    </ul>

    <address class="address">
      2716 Harbor View Lane<br>
      Maple Grove, NY 11420<br>
      <span class="web">www.vantiqo.com</span>
    </address>
  </section>
</body>
</html>
```